Square graphic for social media post

I want to create a 1080 x 1080px all-black image for the quote below that I can share on social media. I want the emphasis to be primarily on the quote, secondarily on the portrait, and third (smallest) on the logo. I want the background on the portrait to be edited so it's transparent and just shows the face of the person on a black background (no brick wall visible).

Graphic color: black
Text color: white
Content: "What we went through is going to make the greatest generation of hoteliers our industry has ever seen." << biggest text
Derek Holm << smaller text
President, Silverbrook Hotels << smaller text
[image of person - use whichever version looks better to you]
[Add Lodging Ledger logo - whichever looks better to you]

This image needs to be readable when sized down much smaller (400x400?) so want the text and portrait to take up most of the space.

I'd like the output both as PNG and original file (preferably Canva). Thanks!

Target Market(s)

Hotel managers

Industry/Entity Type

Hospitality

Font styles to use
Sans Serif

Colors

Designer to choose colors to be used in the design.

Requirements
Must have
• Needs to focus on the quote and the person quoted (the portrait)

```html
<!DOCTYPE html>
<html lang="en">
<head>
<meta charset="utf-8">
<title>Quote Card – Derek Holm</title>
<link href="https://fonts.googleapis.com/css2?family=Bebas+Neue&family=Poppins:wght@300;400;500;700;800&display=swap" rel="stylesheet">
<style>
  :root{
    --page:#e8e8e8;
    --card:#0b0b0b;
    --card-edge:#141414;
    --ink:#ffffff;
    --ink-dark:#1c1c1c;
    --band:#3a3a3a;
    --portrait-light:#8c8c8c;
    --portrait-mid:#555555;
    --portrait-dark:#2a2a2a;
  }
  *{margin:0;padding:0;box-sizing:border-box}
  html,body{width:1200px;height:1200px;overflow:hidden;background:var(--page)}
  .card{
    position:absolute;left:72px;top:71px;width:1058px;height:1058px;
    background:radial-gradient(ellipse at 30% 40%, var(--card-edge), var(--card) 70%);
    overflow:hidden;
  }
  .frame{position:absolute;left:0;top:0;width:1058px;height:1058px}
  .quote-mark{
    position:absolute;left:146px;top:12px;
    font-family:"Poppins",sans-serif;font-weight:800;font-size:300px;line-height:1;color:var(--ink);
  }
  .line{position:absolute;left:153px;color:var(--ink);white-space:nowrap;line-height:1;z-index:2}
  .light{font-family:"Poppins",sans-serif;font-weight:300;font-size:66px;letter-spacing:-1px}
  .l1{top:210px}
  .l2{top:284px}
  .bold{font-family:"Poppins",sans-serif;font-weight:700;font-size:76px;letter-spacing:-2px;top:358px}
  .bars{position:absolute;left:817px;top:292px;width:62px;height:134px}
  .bars span{position:absolute;top:0;width:7px;height:100%;background:var(--ink)}
  .headline{font-family:"Bebas Neue",sans-serif;font-size:172px;top:445px;letter-spacing:1px}
  .sub{font-family:"Bebas Neue",sans-serif;font-size:82px;top:598px;letter-spacing:0.5px}
  .tag{
    position:absolute;left:152px;top:688px;width:683px;height:58px;background:var(--ink);
    font-family:"Poppins",sans-serif;font-weight:700;font-size:44px;letter-spacing:-1.5px;
    color:var(--ink-dark);line-height:58px;padding-left:23px;white-space:nowrap;z-index:2;
  }
  .portrait-head{
    position:absolute;left:846px;top:680px;width:212px;height:300px;
    background:radial-gradient(ellipse 60% 55% at 50% 45%, var(--portrait-light), var(--portrait-mid) 60%, var(--portrait-dark) 100%);
    border-radius:50% 50% 20% 20% / 45% 45% 20% 20%;
    z-index:1;
  }
  .portrait-body{
    position:absolute;left:760px;top:950px;width:298px;height:108px;
    background:linear-gradient(180deg, var(--portrait-mid), var(--portrait-dark));
    border-radius:80px 0 0 0;
    z-index:1;
  }
  .name-band{
    position:absolute;left:294px;top:869px;width:530px;height:62px;
    background:linear-gradient(90deg, transparent, var(--band) 35%, var(--band));
  }
  .name{
    position:absolute;left:455px;top:867px;z-index:2;
    font-family:"Poppins",sans-serif;font-weight:700;font-size:58px;letter-spacing:-1px;color:var(--ink);line-height:1.1;white-space:nowrap;
  }
  .role{
    position:absolute;left:336px;top:944px;z-index:2;
    font-family:"Poppins",sans-serif;font-weight:400;font-size:26px;color:var(--ink);white-space:nowrap;
  }
  .brand{
    position:absolute;left:75px;top:870px;width:220px;text-align:center;
    font-family:"Poppins",sans-serif;font-weight:500;font-size:22px;letter-spacing:6px;color:var(--ink);line-height:1.6;
  }
  .brand-dot{display:block;width:10px;height:10px;border-radius:50%;background:var(--ink);margin:0 auto 10px}
</style>
</head>
<body>
  <main class="card">
    <svg class="frame" viewBox="0 0 1058 1058" aria-hidden="true">
      <polyline points="138,133 68,133 68,817 572,817" fill="none" stroke="#ffffff" stroke-width="3"/>
      <polyline points="313,133 991,133 991,640" fill="none" stroke="#ffffff" stroke-width="3"/>
    </svg>

    <div class="quote-mark" aria-hidden="true">&ldquo;</div>

    <blockquote>
      <div class="line light l1">WHAT WE</div>
      <div class="line light l2">WENT THROUGH IS</div>
      <div class="line bold">GOING TO MAKE</div>
      <div class="line headline">THE GREATEST</div>
      <div class="line sub">GENERATION OF HOTELIERS</div>
      <div class="tag">OUR INDUSTRY HAS EVER SEEN</div>
    </blockquote>

    <div class="bars" aria-hidden="true">
      <span style="left:0"></span><span style="left:27px"></span><span style="left:55px"></span>
    </div>

    <div class="brand"><span class="brand-dot"></span>LODGING<br>LEDGER</div>

    <div class="name-band" aria-hidden="true"></div>
    <div class="name">DEREK HOLM</div>
    <div class="role">President, Silverbrook Hotels</div>

    <div class="portrait-head" role="img" aria-label="Black and white portrait of Derek Holm, smiling, head and shoulders"></div>
    <div class="portrait-body" role="img" aria-label="Derek Holm's dark blazer and open-collar shirt"></div>
  </main>
</body>
</html>
```